Business Card Design

We are a commercial real estate brokerage in San Francisco, leasing office buildings downtown.
I would like a clean, elegant look. Simple but powerful .

Industry/Entity Type

Business

Contact Information for Business Card

Derek Holloway
lic# 07258143
415.555.0172
derek@velt-commercial.example
velt-commercial.example

```html
<!DOCTYPE html>
<html lang="en">
<head>
<meta charset="utf-8">
<title>VELT Commercial – Business Card</title>
<link rel="stylesheet" href="https://fonts.googleapis.com/css2?family=Open+Sans:wght@400;600;700&display=swap">
<style>
  :root {
    --page: #e9eaec;
    --slate-blue: #7e8fae;
    --band-grey: #8a8a8a;
    --paper: #ffffff;
    --ink-dark: #4a4a4a;
    --text-light: #ffffff;
    --rule: #5c5c5c;
  }
  * { box-sizing: border-box; margin: 0; padding: 0; }
  html, body {
    width: 1200px; height: 950px; overflow: hidden;
    background: var(--page);
    font-family: "Open Sans", Arial, sans-serif;
  }
  .sheet {
    width: 1200px; height: 950px;
    display: flex; flex-direction: column;
    align-items: center; justify-content: center; gap: 34px;
  }
  .card {
    width: 760px; height: 434px;
    position: relative; overflow: hidden;
    box-shadow: 0 6px 18px rgba(0,0,0,0.18);
  }

  /* Back side */
  .card--back {
    background: var(--slate-blue);
    display: flex; flex-direction: column;
    align-items: center; justify-content: center;
    color: var(--text-light);
  }
  .back-name {
    font-size: 44px; font-weight: 600; letter-spacing: 2px;
    margin-bottom: 44px;
    display: flex; align-items: center; gap: 18px;
  }
  .back-name .mark-square {
    width: 34px; height: 34px; background: var(--text-light);
  }
  .tagline {
    text-align: center; font-size: 19px; line-height: 1.45; font-weight: 400;
  }

  /* Front side */
  .card--front { background: var(--paper); }
  .brand {
    position: absolute; top: 0; left: 0; right: 0; height: 240px;
    display: flex; align-items: center; justify-content: center; gap: 20px;
  }
  .brand .mark-square {
    width: 56px; height: 56px; background: var(--band-grey);
  }
  .brand-name {
    font-size: 46px; font-weight: 600; letter-spacing: 1px;
    color: var(--slate-blue);
  }
  .name-band {
    position: absolute; top: 240px; left: 0; right: 0; height: 58px;
    background: var(--band-grey);
    display: flex; align-items: center; justify-content: center;
    color: var(--text-light); font-size: 24px; font-weight: 700;
  }
  .contact-band {
    position: absolute; top: 301px; left: 0; right: 0; bottom: 0;
    background: var(--slate-blue);
    display: flex; flex-direction: column; align-items: center; justify-content: center;
    gap: 10px; color: var(--text-light); font-size: 17px;
  }
  .contact-band b { font-weight: 700; }
  .sep { margin: 0 8px; }
</style>
</head>
<body>
<main class="sheet">
  <section class="card card--back" aria-label="Card back">
    <div class="back-name"><span class="mark-square"></span>VELT Commercial</div>
    <p class="tagline">commercial real estate brokerage in San Francisco<br>leasing office buildings downtown.</p>
  </section>

  <section class="card card--front" aria-label="Card front">
    <div class="brand">
      <span class="mark-square"></span>
      <span class="brand-name">VELT Commercial</span>
    </div>
    <div class="name-band">Derek Holloway</div>
    <div class="contact-band">
      <p>lic# 07258143<span class="sep">|</span><b>Phone:</b> 415.555.0172</p>
      <p><b>Email:</b> derek@velt-commercial.example&nbsp;&nbsp;<b>Web:</b> velt-commercial.example</p>
    </div>
  </section>
</main>
</body>
</html>
```